Storm Restoration Contractor needs a professional letterhead design

Looking for a professional letterhead design. Not looking for your cheapo MS Word standard ones that are readily available. Dont want it to be cookie cutter look like ones readily available online. We just recently changed our logo and want to freshen up all our documents. Our company handles restoring a property back to a pre-loss condition after a storm damages it. For example, wind, hail, flood, fire losses.

Target Market(s)

Property Owners, Homeowners, Property Owners, Commercial Property Owners, Property Management Companies

Industry/Entity Type

Construction Company

Requirements
Must have
• Professional, Use 1 of 2 logo options
• Storm Restoration, Roofing, Siding, Windows

```html
<!DOCTYPE html>
<html lang="en">
<head>
<meta charset="utf-8">
<title>Crestline Exteriors Letterhead</title>
<link href="https://fonts.googleapis.com/css2?family=Questrial&display=swap" rel="stylesheet">
<style>
  :root {
    --backdrop: #bdbdbd;
    --paper: #f1f1f1;
    --brand-blue: #246bb0;
    --brand-grey: #4a4a4c;
    --ink: #4a4a4a;
    --watermark: #e7e7e7;
    --white: #ffffff;
  }
  * { box-sizing: border-box; margin: 0; padding: 0; }
  html, body {
    width: 1200px; height: 1041px; overflow: hidden;
    background: var(--backdrop);
    font-family: "Questrial", sans-serif;
  }
  .letterhead {
    position: absolute; left: 200px; top: 4px;
    width: 800px; height: 1033px;
    background: var(--paper);
    overflow: hidden;
  }
  .band-blue { position: absolute; left: 0; top: 0; width: 37px; height: 100%; background: var(--brand-blue); }
  .band-grey { position: absolute; left: 37px; top: 0; width: 12px; height: 100%; background: var(--brand-grey); }
  .watermark { position: absolute; left: 525px; top: -65px; }
  .brand-disc {
    position: absolute; left: 14px; top: 53px;
    width: 84px; height: 84px; border-radius: 50%;
    background: var(--white);
  }
  .brand-divider { position: absolute; left: 105px; top: 60px; width: 2px; height: 70px; background: var(--brand-blue); }
  .brand-name {
    position: absolute; left: 115px; top: 66px;
    color: var(--brand-blue); font-size: 27px; line-height: 27px;
    font-weight: 400; letter-spacing: 1px; text-transform: uppercase;
    white-space: nowrap;
  }
  .contact-tab {
    position: absolute; left: 37px; top: 942px;
    width: 22px; height: 66px; background: var(--brand-blue);
    border-radius: 0 8px 8px 0;
  }
  .contact-icons { position: absolute; left: 40px; top: 946px; }
  .contact-list, .address {
    position: absolute; list-style: none;
    font-size: 11px; line-height: 14px; color: var(--ink);
    white-space: nowrap;
  }
  .contact-list { left: 67px; top: 946px; }
  .address { right: 57px; top: 974px; text-align: right; font-style: normal; }
</style>
</head>
<body>
<main class="letterhead">
  <div class="band-blue"></div>
  <div class="band-grey"></div>

  <svg class="watermark" width="400" height="400" viewBox="0 0 400 400" aria-hidden="true">
    <circle cx="200" cy="200" r="166" fill="none" stroke="var(--watermark)" stroke-width="24"/>
  </svg>

  <header class="brand">
    <div class="brand-disc"></div>
    <div class="brand-divider"></div>
    <h1 class="brand-name">Crestline<br>Exteriors</h1>
  </header>

  <div class="contact-tab"></div>
  <svg class="contact-icons" width="16" height="60" viewBox="0 0 16 60" aria-hidden="true" fill="var(--white)" stroke="var(--white)">
    <path d="M5 3 l2 0 l1 3 l-1.5 1 a6 6 0 0 0 3 3 l1-1.5 l3 1 l0 2 a1.5 1.5 0 0 1 -1.5 1.5 a9 9 0 0 1 -8 -8 a1.5 1.5 0 0 1 1.5 -1.5z" stroke="none" transform="translate(-1,-1) scale(0.8)"/>
    <rect x="5" y="16" width="6" height="3" stroke="none"/>
    <rect x="3" y="19" width="10" height="4" rx="1" stroke="none"/>
    <rect x="3" y="30" width="10" height="6" fill="none" stroke-width="1"/>
    <path d="M3 30 l5 4 l5 -4" fill="none" stroke-width="1"/>
    <circle cx="8" cy="47" r="4.5" fill="none" stroke-width="1"/>
    <path d="M3.5 47 h9 M8 42.5 v9" fill="none" stroke-width="0.8"/>
  </svg>

  <ul class="contact-list">
    <li>555-014-2200</li>
    <li>555-014-2200</li>
    <li>info@crestlineext.com</li>
    <li>www.crestlineext.com</li>
  </ul>

  <address class="address">
    4120 N Meridian Way STE 210<br>
    Tempe, AZ 85281
  </address>
</main>
</body>
</html>
```